German Headhunter/ HR Consultancy needs Business Cards Design

We need a business Card Design for our Company in Stuttgart. We are specialized as Headhunter/ HR Consultancy in Placement of specialist and managers in permanent employment. Please refer to our business logo.

```html
<!DOCTYPE html>
<html lang="en">
<head>
<meta charset="utf-8">
<title>Kernwerk Personalberatung – Business Card</title>
<link href="https://fonts.googleapis.com/css2?family=Montserrat:wght@500;600;700&display=swap" rel="stylesheet">
<style>
  :root {
    --stage: #2a2523;
    --card: #1b1b1d;
    --blue: #3d5bb8;
    --grey: #a9a9ad;
    --white: #ecedf0;
  }
  * { margin: 0; padding: 0; box-sizing: border-box; }
  html, body { width: 1200px; height: 842px; overflow: hidden; }
  body {
    background: var(--stage);
    font-family: "Montserrat", sans-serif;
    display: flex;
    align-items: center;
    justify-content: center;
    gap: 40px;
  }
  .card {
    position: relative;
    width: 540px;
    height: 309px;
    background: var(--card);
    overflow: hidden;
    text-transform: uppercase;
  }
  /* Contact side */
  .card--contact::before,
  .card--contact::after {
    content: "";
    position: absolute;
    left: 0; right: 0;
    height: 12px;
    background: var(--blue);
  }
  .card--contact::before { top: 0; }
  .card--contact::after { bottom: 0; }
  .contact {
    position: absolute;
    top: 12px; bottom: 12px; left: 0; right: 0;
    display: flex;
    flex-direction: column;
    align-items: center;
    justify-content: center;
    text-align: center;
    color: var(--white);
    font-weight: 600;
    padding-bottom: 14px;
  }
  .contact__name { color: var(--blue); font-size: 26px; font-weight: 700; letter-spacing: 0.5px; line-height: 1; }
  .contact__role { font-size: 15px; margin-top: 5px; letter-spacing: 0.4px; }
  .contact__rule { width: 70px; height: 2px; background: var(--blue); margin: 12px 0; }
  .contact__line { font-size: 17px; line-height: 1.25; letter-spacing: 0.3px; }
  .contact__line--phone { font-size: 20px; }

  /* Brand side */
  .edge-mark { position: absolute; display: flex; height: 58px; }
  .edge-mark__block { width: 40px; background: var(--blue); }
  .edge-mark__bar { width: 6px; background: var(--grey); margin: 0 4px; }
  .edge-mark--left { left: 0; top: 150px; }
  .edge-mark--right { right: 0; top: 70px; flex-direction: row-reverse; }
  .brand {
    position: absolute;
    inset: 0;
    display: flex;
    align-items: center;
    justify-content: center;
    gap: 14px;
  }
  .brand__square { width: 34px; height: 34px; background: var(--blue); }
  .brand__name {
    color: var(--blue);
    font-size: 22px;
    font-weight: 600;
    letter-spacing: 1px;
    line-height: 1.2;
  }
</style>
</head>
<body>
  <section class="card card--contact">
    <div class="contact">
      <p class="contact__name">Lukas Brenner</p>
      <p class="contact__role">Managing Director</p>
      <span class="contact__rule"></span>
      <p class="contact__line contact__line--phone">0711-482 903 517</p>
      <p class="contact__line">info@kernwerk.de</p>
      <p class="contact__line">www.kernwerk-hr.de</p>
      <span class="contact__rule"></span>
      <p class="contact__line">58, Lindenallee Nord</p>
      <p class="contact__line">70173, Deutschland</p>
    </div>
  </section>

  <section class="card card--brand">
    <div class="edge-mark edge-mark--left">
      <span class="edge-mark__block"></span>
      <span class="edge-mark__bar"></span>
    </div>
    <div class="edge-mark edge-mark--right">
      <span class="edge-mark__block"></span>
      <span class="edge-mark__bar"></span>
    </div>
    <div class="brand">
      <span class="brand__square"></span>
      <p class="brand__name">Kernwerk<br>Personalberatung</p>
    </div>
  </section>
</body>
</html>
```